Leaflet to promote a new sports massage business

I am a Remedial and Sports Massage therapist and treat a range of people from professionals who spend hours working behind computers and have associated neck and back pain through poor posture to amateur sports people of varying intensity/ability - who encounter injuries along the way, or just need some good old stretching out.Remedial and sports massage helps people who have musculoskeletal injury, pain or dysfunction brought about by the stresses and strains of life. Through massage i can reduce pain, promote recovery after injury, relieve stress, and improve flexibility. All of this contributes to helping people feel better. I have just started working at a new location (address attached) and am looking to raise awareness that I am there and to promote the benefits of massage to encourage new clients(attached as a separate document). I have a business card (attached to the brief) which uses hands as the main device, I would like to include these – possibly in some sort of logo and I would like to use purple as a key colour (if colour is used). I also want to include the KTVB logo (attached) to add credibility

```html
<!DOCTYPE html>
<html lang="en">
<head>
<meta charset="utf-8">
<title>Benefits of Massage – Danielle Harwood</title>
<link rel="stylesheet" href="https://fonts.googleapis.com/css2?family=Roboto+Condensed:wght@700&family=Lato:wght@300;400&display=swap">
<style>
  :root {
    --gold-dark: #a88448;
    --gold-light: #ecdcb6;
    --purple-deep: #55174a;
    --purple: #7b2d6b;
    --purple-text: #6a2060;
    --ink: #3a3a3a;
    --white: #ffffff;
    --skin: #e8c7ad;
  }
  * { margin: 0; padding: 0; box-sizing: border-box; }
  html, body { width: 769px; height: 1200px; overflow: hidden; background: var(--white); }
  .leaflet {
    position: relative; width: 769px; height: 1200px; overflow: hidden;
    background: linear-gradient(160deg, var(--gold-dark), var(--gold-light) 45%, var(--gold-dark));
    font-family: "Lato", sans-serif;
  }
  .sheet {
    position: absolute; left: 20px; top: 20px; width: 729px; height: 1012px;
    background: var(--white); overflow: hidden;
  }
  .hero-photo {
    position: absolute; left: 0; top: 0; width: 729px; height: 467px;
    background: linear-gradient(135deg, #fbf8f6 0%, #f2e6dc 35%, var(--skin) 60%, #d8ad90 80%, #f4eee9 100%);
  }
  .accreditation {
    position: absolute; right: 24px; top: 30px;
    display: flex; align-items: center; gap: 10px;
  }
  .accreditation-dot { width: 26px; height: 26px; border-radius: 50%; background: var(--purple); }
  .accreditation-name { font-weight: 400; font-size: 32px; color: var(--purple); letter-spacing: 2px; }
  .benefits-title {
    position: absolute; left: 0; top: 467px; width: 729px; height: 56px;
    background: var(--purple-deep); color: var(--white);
    font-family: "Roboto Condensed", sans-serif; font-weight: 700; font-size: 37px;
    text-align: center; line-height: 56px; letter-spacing: 1px;
  }
  .benefits-list {
    position: absolute; left: 0; top: 523px; width: 729px; height: 226px;
    background: var(--purple); list-style: none; padding-top: 9px;
  }
  .benefits-list li {
    display: flex; justify-content: center; align-items: center; gap: 12px;
    height: 42px; color: var(--white);
    font-family: "Roboto Condensed", sans-serif; font-weight: 700; font-size: 27px;
  }
  .benefits-list svg { width: 24px; height: 24px; flex: none; }
  .brand-hands {
    position: absolute; left: 0; top: 752px; width: 236px; height: 260px;
    background: radial-gradient(ellipse at 45% 50%, var(--purple) 0%, #9a4f8a 55%, #f3e6ef 100%);
  }
  .therapist {
    position: absolute; left: 246px; top: 768px; width: 476px;
    color: var(--ink); text-align: center;
  }
  .therapist-name {
    font-weight: 300; font-size: 40px; line-height: 44px; color: var(--purple-text);
    letter-spacing: 1px; white-space: nowrap;
  }
  .therapist-role { font-weight: 400; font-size: 21px; line-height: 26px; color: var(--purple-text); white-space: nowrap; }
  .therapist-address { font-size: 15px; line-height: 20px; margin-top: 8px; }
  .contact-list { list-style: none; margin-top: 8px; display: inline-block; text-align: left; }
  .contact-list li { display: flex; align-items: center; gap: 10px; font-size: 15px; height: 28px; white-space: nowrap; }
  .contact-list svg { width: 18px; height: 18px; flex: none; }
  .reflection {
    position: absolute; left: 20px; top: 1032px; width: 729px; height: 168px; overflow: hidden;
    background: linear-gradient(to bottom, rgba(255,255,255,.7), rgba(255,255,255,0));
  }
  .reflection-hands {
    position: absolute; left: 0; top: 0; width: 236px; height: 110px; opacity: .3;
    background: linear-gradient(to bottom, #9a4f8a, rgba(154,79,138,0));
  }
  .reflection-contacts {
    position: absolute; left: 0; top: 4px; width: 729px; padding-left: 246px;
    text-align: center; transform: scaleY(-1); transform-origin: 50% 42px; opacity: .25; color: var(--ink);
  }
  .reflection-contacts .contact-list { margin-top: 0; }
</style>
</head>
<body>
<main class="leaflet">
  <section class="sheet">
    <div class="hero-photo" role="img" aria-label="Photograph of a therapist's hands massaging a client's leg"></div>
    <div class="accreditation">
      <span class="accreditation-dot"></span>
      <span class="accreditation-name">KTVB</span>
    </div>

    <h1 class="benefits-title">BENEFITS OF MASSAGE</h1>
    <ul class="benefits-list">
      <li><svg viewBox="0 0 26 26"><rect x="2" y="2" width="22" height="22" fill="none" stroke="#fff" stroke-width="2.5"/><path d="M7 13l4 5 8-11" fill="none" stroke="#fff" stroke-width="3"/></svg>Reduces Pain</li>
      <li><svg viewBox="0 0 26 26"><rect x="2" y="2" width="22" height="22" fill="none" stroke="#fff" stroke-width="2.5"/><path d="M7 13l4 5 8-11" fill="none" stroke="#fff" stroke-width="3"/></svg>Promotes Recovery</li>
      <li><svg viewBox="0 0 26 26"><rect x="2" y="2" width="22" height="22" fill="none" stroke="#fff" stroke-width="2.5"/><path d="M7 13l4 5 8-11" fill="none" stroke="#fff" stroke-width="3"/></svg>Improves Posture and Flexibility</li>
      <li><svg viewBox="0 0 26 26"><rect x="2" y="2" width="22" height="22" fill="none" stroke="#fff" stroke-width="2.5"/><path d="M7 13l4 5 8-11" fill="none" stroke="#fff" stroke-width="3"/></svg>Relieves Stress</li>
      <li><svg viewBox="0 0 26 26"><rect x="2" y="2" width="22" height="22" fill="none" stroke="#fff" stroke-width="2.5"/><path d="M7 13l4 5 8-11" fill="none" stroke="#fff" stroke-width="3"/></svg>Improves Health and Wellbeing</li>
    </ul>

    <div class="brand-hands" role="img" aria-label="Illustration of two purple hands, the therapist's brand device"></div>
    <div class="therapist">
      <h2 class="therapist-name">DANIELLE HARWOOD</h2>
      <p class="therapist-role">Remedial and Sports Massage Therapist</p>
      <p class="therapist-address">Peak Motion Physiotherapy<br>Riverside Sports Ground<br>Elm Meadow Road, Ashford, AB1 2CD</p>
      <ul class="contact-list">
        <li><svg viewBox="0 0 20 20"><circle cx="10" cy="10" r="10" fill="#3a3a3a"/><path d="M7 5c1 0 1.5 2 1.5 2.5S7.5 8.5 7.5 9c0 1 2.5 3.5 3.5 3.5.5 0 1-1 1.5-1s2.5.5 2.5 1.5-1 2-2 2C10 15 5 10 5 7c0-1 1-2 2-2z" fill="#fff"/></svg>07700 900412</li>
        <li><svg viewBox="0 0 20 20"><circle cx="10" cy="10" r="10" fill="#3a3a3a"/><rect x="5" y="6.5" width="10" height="7" fill="none" stroke="#fff" stroke-width="1.3"/><path d="M5 6.5l5 4 5-4" fill="none" stroke="#fff" stroke-width="1.3"/></svg>danielleharwood@mailbox.net</li>
        <li><svg viewBox="0 0 20 20"><circle cx="10" cy="10" r="10" fill="#3a3a3a"/></svg>follow/HarwoodMassage</li>
      </ul>
    </div>
  </section>

  <div class="reflection" aria-hidden="true">
    <div class="reflection-hands"></div>
    <div class="reflection-contacts">
      <ul class="contact-list">
        <li><svg viewBox="0 0 20 20"><circle cx="10" cy="10" r="10" fill="#3a3a3a"/></svg>07700 900412</li>
        <li><svg viewBox="0 0 20 20"><circle cx="10" cy="10" r="10" fill="#3a3a3a"/></svg>danielleharwood@mailbox.net</li>
        <li><svg viewBox="0 0 20 20"><circle cx="10" cy="10" r="10" fill="#3a3a3a"/></svg>follow/HarwoodMassage</li>
      </ul>
    </div>
  </div>
</main>
</body>
</html>
```